Construction Company

Design a clutter free business card, it can be double-sided utilizing the logo for VKM Ltd simple with all relevant contact information.

Please also a letterhead design to function for the purposes of invoicing, all mail requirements, with header to be distinctive while the footer ties page together and incorporates all necessary information.

For now, please use generic / dummy text and when a winner is selected, I will disclose the contact information.

Hi Designers! Please read the updated brief which includes the design of a business card and letterhead. Thank you!

```html
<!DOCTYPE html>
<html lang="en">
<head>
<meta charset="utf-8">
<title>VKM Ltd — Letterhead and Business Card</title>
<link rel="stylesheet" href="https://fonts.googleapis.com/css2?family=Libre+Baskerville:wght@400;700&family=Open+Sans:wght@400;600&display=swap">
<style>
  :root {
    --navy: #243c8a;
    --navy-deep: #1c2f70;
    --gold: #b08d2c;
    --paper: #ffffff;
    --backdrop: #e9eaec;
    --body-text: #8a8a8a;
    --contact-text: #3a3a3a;
    --mark-light: #c9cdea;
  }
  * { box-sizing: border-box; margin: 0; padding: 0; }
  html, body { width: 1200px; height: 800px; overflow: hidden; }
  body {
    background: var(--backdrop);
    font-family: "Open Sans", Arial, sans-serif;
    position: relative;
  }

  /* Letterhead */
  .letterhead {
    position: absolute; left: 70px; top: 28px;
    width: 524px; height: 744px;
    background: var(--paper);
    box-shadow: 0 2px 10px rgba(0,0,0,.12);
  }
  .letterhead .brand {
    position: absolute; left: 46px; top: 48px;
    font-family: "Libre Baskerville", Georgia, serif;
    font-weight: 700; font-size: 34px; color: var(--navy);
    letter-spacing: 1px;
  }
  .letterhead .contact {
    position: absolute; right: 40px; top: 150px;
    list-style: none; font-size: 10.5px; color: var(--contact-text);
    line-height: 1.55;
  }
  .contact li { display: flex; align-items: center; gap: 6px; }
  .contact svg { width: 10px; height: 10px; fill: var(--navy); flex: none; }
  .letter {
    position: absolute; left: 46px; top: 200px; right: 46px;
    font-size: 8.6px; line-height: 1.55; color: var(--body-text);
  }
  .letter p { margin-bottom: 9px; }
  .letter .sign-off { margin-top: 14px; }
  .footer-band {
    position: absolute; left: 0; right: 0; bottom: 34px; height: 30px;
    background: var(--navy); color: #fff;
    display: flex; align-items: center; gap: 8px;
    padding-left: 60px; font-size: 11.5px; font-weight: 600;
  }
  .footer-band svg { width: 11px; height: 11px; fill: #fff; }
  .footer-tab {
    position: absolute; right: 0; bottom: 20px; width: 70px; height: 16px;
    background: var(--gold);
  }

  /* Business cards */
  .card {
    position: absolute; left: 650px; width: 490px; height: 280px;
    box-shadow: 0 2px 10px rgba(0,0,0,.14);
  }
  .card-front { top: 100px; background: var(--paper); }
  .card-front .brand {
    position: absolute; left: 58px; top: 88px;
    font-family: "Libre Baskerville", Georgia, serif;
    font-weight: 700; font-size: 32px; color: var(--navy);
  }
  .card-front .divider {
    position: absolute; left: 262px; top: 70px; width: 1px; height: 110px;
    background: var(--navy);
  }
  .card-front .person { position: absolute; left: 282px; top: 74px; }
  .person .name {
    font-family: "Libre Baskerville", Georgia, serif;
    font-weight: 700; font-size: 14px; color: var(--navy); letter-spacing: .5px;
  }
  .person .role { font-size: 10.5px; font-weight: 600; color: var(--gold); margin-bottom: 10px; }
  .person .contact { list-style: none; font-size: 10.5px; color: var(--contact-text); line-height: 1.6; }
  .card-front .footer-band { bottom: 36px; height: 26px; padding-left: 28px; font-size: 10px; }
  .card-front .footer-tab { bottom: 22px; width: 60px; height: 14px; }

  .card-back {
    top: 410px; background: var(--navy);
    display: flex; align-items: center; justify-content: center;
  }
  .card-back .brand {
    font-family: "Libre Baskerville", Georgia, serif;
    font-weight: 700; font-size: 44px; color: var(--mark-light); letter-spacing: 1px;
  }
</style>
</head>
<body>

<svg width="0" height="0" style="position:absolute">
  <defs>
    <symbol id="icon-phone" viewBox="0 0 24 24"><path d="M6.6 10.8a15 15 0 0 0 6.6 6.6l2.2-2.2c.3-.3.7-.4 1-.2 1.1.4 2.3.6 3.6.6.6 0 1 .4 1 1V20c0 .6-.4 1-1 1A17 17 0 0 1 3 4c0-.6.4-1 1-1h3.5c.6 0 1 .4 1 1 0 1.3.2 2.5.6 3.6.1.3 0 .7-.2 1z"/></symbol>
    <symbol id="icon-mail" viewBox="0 0 24 24"><path d="M2 5h20v14H2zm2 2v.5l8 5 8-5V7l-8 5z"/></symbol>
    <symbol id="icon-web" viewBox="0 0 24 24"><path d="M12 2a10 10 0 1 0 0 20 10 10 0 0 0 0-20zm1 17.9V18h-2v1.9A8 8 0 0 1 4.1 13H6v-2H4.1A8 8 0 0 1 11 4.1V6h2V4.1a8 8 0 0 1 6.9 6.9H18v2h1.9a8 8 0 0 1-6.9 6.9z"/></symbol>
    <symbol id="icon-pin" viewBox="0 0 24 24"><path d="M12 2a7 7 0 0 0-7 7c0 5 7 13 7 13s7-8 7-13a7 7 0 0 0-7-7zm0 9.5A2.5 2.5 0 1 1 12 6.5a2.5 2.5 0 0 1 0 5z"/></symbol>
  </defs>
</svg>

<section class="letterhead" aria-label="Letterhead">
  <div class="brand">VKM Ltd</div>
  <ul class="contact">
    <li><svg><use href="#icon-phone"/></svg>020.555.0148</li>
    <li><svg><use href="#icon-mail"/></svg>info@vkmltd.com</li>
    <li><svg><use href="#icon-web"/></svg>www.vkmltd.com</li>
  </ul>
  <div class="letter">
    <p>Dear customer,</p>
    <p>Lorem ipsum dolor sit amet, consectetur adipisicing elit, sed do eiusmod tempor incididunt ut labore et dolore magna aliqua. Ut enim ad minim veniam, quis nostrud exercitation ullamco laboris nisi ut aliquip ex ea commodo consequat. Duis aute irure dolor in reprehenderit in voluptate velit esse cillum dolore eu fugiat nulla pariatur. Excepteur sint occaecat cupidatat non proident, sunt in culpa qui officia deserunt mollit anim id est laborum.</p>
    <p>Lorem ipsum dolor sit amet, consectetur adipisicing elit, sed do eiusmod tempor incididunt ut labore et dolore magna aliqua. Ut enim ad minim veniam, quis nostrud exercitation ullamco laboris nisi ut aliquip ex ea commodo consequat. Duis aute irure dolor in reprehenderit in voluptate velit esse cillum dolore eu fugiat nulla pariatur. Excepteur sint occaecat cupidatat non proident, sunt in culpa qui officia deserunt mollit anim id est laborum.</p>
    <p>Lorem ipsum dolor sit amet, consectetur adipisicing elit, sed do eiusmod tempor incididunt ut labore et dolore magna aliqua. Ut enim ad minim veniam, quis nostrud exercitation ullamco laboris nisi ut aliquip ex ea commodo consequat. Duis aute irure dolor in reprehenderit in voluptate velit esse cillum dolore eu fugiat nulla pariatur. Excepteur sint occaecat cupidatat non proident, sunt in culpa qui officia deserunt mollit anim id est laborum.</p>
    <p>Lorem ipsum dolor sit amet, consectetur adipisicing elit, sed do eiusmod tempor incididunt ut labore et dolore magna aliqua. Ut enim ad minim veniam, quis nostrud exercitation ullamco laboris nisi ut aliquip ex ea commodo consequat. Duis aute irure dolor in reprehenderit.</p>
    <p class="sign-off">Yours Sincerely,</p>
  </div>
  <div class="footer-band"><svg><use href="#icon-pin"/></svg>Harbour House, 12 Mill Lane, London, SE2 4PX</div>
  <div class="footer-tab"></div>
</section>

<section class="card card-front" aria-label="Business card front">
  <div class="brand">VKM Ltd</div>
  <div class="divider"></div>
  <div class="person">
    <div class="name">DANIEL REED</div>
    <div class="role">Director</div>
    <ul class="contact">
      <li><svg><use href="#icon-phone"/></svg>020.555.0148</li>
      <li><svg><use href="#icon-mail"/></svg>info@vkmltd.com</li>
      <li><svg><use href="#icon-web"/></svg>www.vkmltd.com</li>
    </ul>
  </div>
  <div class="footer-band"><svg><use href="#icon-pin"/></svg>Harbour House, 12 Mill Lane, London, SE2 4PX</div>
  <div class="footer-tab"></div>
</section>

<section class="card card-back" aria-label="Business card back">
  <div class="brand">VKM Ltd</div>
</section>

</body>
</html>
```